LHP Regal Business Card Design 2020

Your Manor Steward is looking for a business card that is clean and straight to the point but still looks high-end and attractive. We are a team comprised of management and field professionals focused on the high-end residential marketplace. We serve homeowners and trade professionals directly based out of the Metrowest/Boston area. We provide client services as well as construction/renovation services.
We are aiming for a black and white feel (white background and black text) and a matte finish with rounded edges.

We want to emphasis our vision of "Properties - Projects - Partners".
Dana Pellham is the president of LHP

Please include the following areas we service: Boston/Cape/Newport
Please make sure to include Dana's mobile (555) 213 4480 & office number (555) 640 1937, email dana@yourmanorsteward.example and website www.yourmanorsteward.example

Colors

Designer to choose only greyscale colors for use in the design.

Requirements
Must have
• Include "Properties - Projects - Partners" in design

Include "After Hours Emergency Support # 1800 555 0142" with icon

```html
<!DOCTYPE html>
<html lang="en">
<head>
<meta charset="utf-8">
<title>Your Manor Steward – Business Card</title>
<link rel="stylesheet" href="https://fonts.googleapis.com/css2?family=Montserrat:wght@600;700&family=Raleway:wght@700&family=Roboto:wght@400;500&display=swap">
<style>
  :root {
    --page: #e4e4e4;
    --card-light: #ffffff;
    --card-dark: #2b2b2b;
    --ink: #2a2a2a;
    --ink-soft: #333333;
    --ink-muted: #555555;
    --mark-on-dark: #b9b9b9;
    --text-on-dark: #f2f2f2;
  }
  * { margin: 0; padding: 0; box-sizing: border-box; }
  html, body { width: 1173px; height: 1200px; overflow: hidden; background: var(--page); }
  .card { position: absolute; width: 744px; height: 411px; overflow: hidden; }
  .card--front { left: 204px; top: 150px; background: var(--card-light); }
  .card--back { left: 204px; top: 637px; background: var(--card-dark); }

  .brand-name {
    position: absolute; font-family: "Montserrat", sans-serif; font-weight: 700;
    line-height: 1; white-space: nowrap;
  }
  .card--front .brand-name { left: 60px; top: 35px; font-size: 130px; color: var(--ink); }
  .brand-tagline {
    position: absolute; font-family: "Montserrat", sans-serif; font-weight: 600;
    white-space: nowrap;
  }
  .card--front .brand-tagline { left: 76px; top: 161px; font-size: 16.5px; letter-spacing: 1.7px; color: var(--ink); }

  .vision {
    position: absolute; right: 66px; top: 62px;
    font-family: "Montserrat", sans-serif; font-weight: 600; font-size: 14px;
    letter-spacing: 1.2px; color: var(--ink-muted); white-space: nowrap;
  }
  .emergency {
    position: absolute; right: 66px; top: 92px; display: flex; align-items: center;
    font-family: "Roboto", sans-serif; font-size: 14px; color: var(--ink-soft); white-space: nowrap;
  }
  .emergency svg { width: 16px; height: 16px; margin-right: 7px; fill: var(--ink-soft); flex: none; }

  .contact-list { position: absolute; left: 65px; top: 258px; list-style: none; }
  .contact-list li {
    display: flex; align-items: center; height: 25px;
    font-family: "Roboto", sans-serif; font-size: 20.5px; color: var(--ink-soft); white-space: nowrap;
  }
  .contact-list svg { width: 17px; height: 17px; margin-right: 10px; fill: var(--ink-soft); flex: none; }

  .holder { position: absolute; right: 66px; top: 278px; text-align: right; }
  .holder-name { font-family: "Raleway", sans-serif; font-weight: 700; font-size: 28px; line-height: 1.15; color: var(--ink); letter-spacing: 0.3px; white-space: nowrap; }
  .holder-role { font-family: "Roboto", sans-serif; font-weight: 500; font-size: 21px; color: var(--ink-soft); margin-right: 6px; }
  .edge-tab { position: absolute; right: 0; top: 285px; width: 22px; height: 45px; background: var(--ink); }

  .card--back .brand-name {
    left: 0; right: 0; top: 104px; text-align center; text-align: center; font-size: 170px; color: var(--mark-on-dark);
  }
  .card--back .brand-tagline {
    left: 0; right: 0; top: 271px; text-align: center; font-size: 21.5px; letter-spacing: 2.6px; color: var(--mark-on-dark);
  }
  .service-areas {
    position: absolute; left: 0; right: 0; top: 358px; text-align: center;
    font-family: "Roboto", sans-serif; font-size: 19.5px; color: var(--text-on-dark); white-space: nowrap;
  }
  .service-areas span::before { content: "\25CF"; font-size: 12px; margin: 0 6px 0 4px; vertical-align: 2px; }
</style>
</head>
<body>
  <section class="card card--front">
    <div class="brand-name">LHP</div>
    <div class="brand-tagline">YOUR MANOR STEWARD</div>

    <div class="vision">PROPERTIES – PROJECTS – PARTNERS</div>
    <div class="emergency"><svg viewBox="0 0 16 16"><path d="M8 .5 15.5 15H.5zm-.9 5v5h1.8v-5zm0 6.3v1.8h1.8v-1.8z"/></svg>After Hours Emergency Support # 1800 555 0142</div>

    <ul class="contact-list">
      <li><svg viewBox="0 0 16 16"><path d="M4 0h8a1.5 1.5 0 0 1 1.5 1.5v13A1.5 1.5 0 0 1 12 16H4a1.5 1.5 0 0 1-1.5-1.5v-13A1.5 1.5 0 0 1 4 0zm0 2v10.5h8V2zm4 11.2a.9.9 0 1 0 0 1.8.9.9 0 0 0 0-1.8z"/></svg>(555) 213 4480</li>
      <li><svg viewBox="0 0 16 16"><path d="M1 4c0-1.5 3-3 7-3s7 1.5 7 3v1.5h-3.5V4h-7v1.5H1zM4.5 6.5h7L14 10v5H2v-5zM8 9a2 2 0 1 0 0 4 2 2 0 0 0 0-4z"/></svg>(555) 640 1937</li>
      <li><svg viewBox="0 0 16 16"><path d="M0 3h16v10H0zm1.4 1.2L8 9l6.6-4.8zm-.4 1.3v6.3l4.3-3.2zm14 0l-4.3 3.1 4.3 3.2zM6 8.7l-4.6 3.3h13.2L10 8.7 8 10.2z"/></svg>dana@yourmanorsteward.example</li>
      <li><svg viewBox="0 0 16 16"><path d="M8 0a8 8 0 1 0 0 16A8 8 0 0 0 8 0zm-1 2.2c.5.8-.6 1.4-1.2 2.1-.5.6.4 1.2-.3 1.8-.8.6-2 .3-2.4 1.2-.4.8.6 1.5 1.4 1.7.9.2 1.5 1 1.3 2-.2.8.4 1.7.2 2.6A6 6 0 0 1 7 2.2zm3.5.6A6 6 0 0 1 13.9 9c-.6-.4-1.1-1.2-1.9-1-.9.2-1.6-.6-1.4-1.4.2-.7 1.2-.8 1.3-1.6.1-.7-.8-1-1.4-1.3z"/></svg>www.yourmanorsteward.example</li>
    </ul>

    <div class="holder">
      <div class="holder-name">DANA PELLHAM</div>
      <div class="holder-role">President</div>
    </div>
    <div class="edge-tab"></div>
  </section>

  <section class="card card--back">
    <div class="brand-name">LHP</div>
    <div class="brand-tagline">YOUR MANOR STEWARD</div>
    <div class="service-areas"><span>Boston</span> <span>Metrowest</span> <span>South Shore</span> <span>Cape</span> <span>Newport</span></div>
  </section>
</body>
</html>
```